TalkHarbor - Language Coaching Services

Sleek, innovative, trendy design for Language Coaching business.

TalkHarbor is a new UK based company that provides Language Coaching services. We offer highly personalized on-line and face to face language courses. We also impart learning techniques workshops based on the latest neuroscience research for second-language acquisition.

Target Market(s)

See attached info

Industry/Entity Type

Consulting

Contact Information for Business Card

TalkHarbor
DaniaKV@talkharbor.co.uk
TalkHarbor.co.uk
London, UK

Font styles to use
Sans Serif

```html
<!DOCTYPE html>
<html lang="en">
<head>
<meta charset="utf-8">
<title>TalkHarbor Business Card</title>
<link rel="stylesheet" href="https://fonts.googleapis.com/css2?family=Open+Sans:wght@400;600;700&display=swap">
<style>
  :root {
    --backdrop: #4a403b;
    --card: #1c1f23;
    --silver: #d4d6d8;
    --blue: #1a8cc4;
    --white: #f2f2f2;
    --rule: #e8e8e8;
  }
  html, body {
    margin: 0;
    padding: 0;
    width: 1200px;
    height: 864px;
    overflow: hidden;
    background: var(--backdrop);
    font-family: "Open Sans", sans-serif;
  }
  .canvas {
    position: relative;
    width: 1200px;
    height: 864px;
  }
  .card {
    position: absolute;
    width: 520px;
    height: 300px;
    background: var(--card);
    box-shadow: 0 10px 24px rgba(0,0,0,0.35);
  }
  /* Back side */
  .card-back { left: 60px; top: 120px; }
  .back-mark {
    position: absolute;
    left: 0; right: 0; top: 48px;
    display: flex;
    flex-direction: column;
    align-items: center;
  }
  .back-mark .ring {
    width: 120px; height: 120px;
    border: 8px solid var(--silver);
    border-radius: 50%;
    box-sizing: border-box;
  }
  .back-mark .brand {
    margin-top: 14px;
    color: var(--silver);
    font-weight: 600;
    font-size: 26px;
    letter-spacing: 1px;
  }
  .back-url {
    position: absolute;
    left: 0; right: 0; bottom: 34px;
    text-align: center;
    color: var(--silver);
    font-size: 13px;
    letter-spacing: 5px;
  }
  /* Front side */
  .card-front { left: 620px; top: 444px; }
  .person {
    position: absolute;
    left: 40px; top: 118px;
  }
  .person .name {
    color: var(--blue);
    font-weight: 700;
    font-size: 19px;
    line-height: 22px;
    text-transform: uppercase;
  }
  .person .role {
    color: var(--white);
    font-size: 15px;
    line-height: 18px;
    text-transform: uppercase;
  }
  .rule {
    position: absolute;
    left: 40px; right: 48px; top: 184px;
    height: 2px;
    background: var(--rule);
  }
  .contacts {
    position: absolute;
    left: 40px; top: 196px;
    margin: 0; padding: 0;
    list-style: none;
  }
  .contacts li {
    display: flex;
    align-items: center;
    color: var(--white);
    font-size: 15px;
    line-height: 24px;
  }
  .contacts svg {
    width: 13px; height: 13px;
    margin-right: 9px;
    fill: var(--blue);
    flex: none;
  }
  .front-mark {
    position: absolute;
    right: 40px; top: 52px;
    display: flex;
    align-items: center;
    gap: 12px;
  }
  .front-mark .brand {
    color: var(--blue);
    font-weight: 600;
    font-size: 28px;
    letter-spacing: 1px;
  }
  .front-mark .ring {
    width: 68px; height: 68px;
    border: 5px solid var(--blue);
    border-radius: 50%;
    box-sizing: border-box;
  }
</style>
</head>
<body>
<main class="canvas">
  <section class="card card-back" aria-label="Card back">
    <div class="back-mark">
      <div class="ring"></div>
      <div class="brand">TalkHarbor</div>
    </div>
    <div class="back-url">www.talkharbor.co.uk</div>
  </section>

  <section class="card card-front" aria-label="Card front">
    <div class="front-mark">
      <div class="brand">TalkHarbor</div>
      <div class="ring"></div>
    </div>
    <div class="person">
      <div class="name">Elin Marsh</div>
      <div class="role">President</div>
    </div>
    <div class="rule"></div>
    <ul class="contacts">
      <li>
        <svg viewBox="0 0 16 16" aria-hidden="true"><path d="M4 0h8a1.5 1.5 0 0 1 1.5 1.5v13A1.5 1.5 0 0 1 12 16H4a1.5 1.5 0 0 1-1.5-1.5v-13A1.5 1.5 0 0 1 4 0zm0 2v10h8V2H4zm4 11a1 1 0 1 0 0 2 1 1 0 0 0 0-2z"/></svg>
        020 7946 0183
      </li>
      <li>
        <svg viewBox="0 0 16 16" aria-hidden="true"><path d="M0 3h16v1.2L8 9 0 4.2V3zm0 3l8 4.8L16 6v7H0V6z"/></svg>
        info@talkharbor.co.uk
      </li>
      <li>
        <svg viewBox="0 0 16 16" aria-hidden="true"><path d="M8 0a8 8 0 1 0 0 16A8 8 0 0 0 8 0zm0 1.6c.9 0 2 1.9 2.3 4.8H5.7C6 3.5 7.1 1.6 8 1.6zM5.7 9.6h4.6C10 12.5 8.9 14.4 8 14.4S6 12.5 5.7 9.6zM1.7 6.4h2.4a14 14 0 0 0 0 3.2H1.7a6.4 6.4 0 0 1 0-3.2zm10.2 0h2.4a6.4 6.4 0 0 1 0 3.2h-2.4a14 14 0 0 0 0-3.2z"/></svg>
        TalkHarbor.co.uk
      </li>
    </ul>
  </section>
</main>
</body>
</html>
```